We are a recruitment company based in Norwich/Cambridge England.
I have included our company logo which we want to remain the same.

What we are looking for is a new creative Business card which will really stand out!!

Contact Information for Business Card

Harriet Dunmore
email: Harriet@plavex.co.uk
Address: Brackwell House
Fenmoor Enterprise Park
Partridge Way
Norwich
QB9 3KX
Tel:01632 960418

```html
<!DOCTYPE html>
<html lang="en">
<head>
<meta charset="utf-8">
<title>Plavex Business Card</title>
<link rel="stylesheet" href="https://fonts.googleapis.com/css2?family=Roboto:wght@400;500&family=Roboto+Condensed:wght@400;700&display=swap">
<style>
  :root {
    --backdrop: #2b2b2b;
    --brand-green: #8dc63f;
    --brand-grey: #8e898f;
    --ring-grey: #8c878d;
    --panel-light: #efefef;
    --white: #ffffff;
  }
  * { margin: 0; padding: 0; box-sizing: border-box; }
  html, body {
    width: 1200px; height: 960px; overflow: hidden;
    background: var(--backdrop);
  }
  .canvas { position: relative; width: 1200px; height: 960px; }
  .card {
    position: absolute; width: 600px; height: 342px; overflow: hidden;
    font-family: "Roboto", Arial, sans-serif; color: var(--white);
  }
  .card--front { left: 322px; top: 108px; background: var(--brand-green); }
  .card--back { left: 320px; top: 493px; background: var(--brand-grey); }
  .front-shape { position: absolute; inset: 0; }
  .contact-block { position: absolute; left: 26px; top: 73px; }
  .person-name {
    font-family: "Roboto Condensed", "Arial Narrow", sans-serif;
    font-weight: 700; font-size: 21px; line-height: 24px; letter-spacing: 0.2px;
  }
  .person-role {
    font-family: "Roboto Condensed", "Arial Narrow", sans-serif;
    font-weight: 400; font-size: 15.5px; line-height: 18px;
  }
  .address { margin-top: 12px; font-size: 14.5px; line-height: 19px; }
  .contact-list { list-style: none; margin-top: 10px; }
  .contact-item { display: flex; align-items: center; font-size: 14.5px; line-height: 19px; }
  .contact-icon { width: 14px; height: 14px; margin-right: 10px; fill: var(--white); }
  .brand-lockup {
    position: absolute; left: 296px; top: 150px;
    display: flex; align-items: center; gap: 10px;
  }
  .brand-dot { width: 34px; height: 34px; border-radius: 50%; background: var(--brand-green); }
  .brand-name {
    font-family: "Roboto", Arial, sans-serif; font-weight: 500;
    font-size: 40px; line-height: 1; color: var(--ring-grey);
  }
  .back-lockup {
    position: absolute; left: 0; right: 0; top: 130px;
    display: flex; justify-content: center; align-items: center; gap: 16px;
  }
  .back-lockup .brand-dot { width: 56px; height: 56px; background: var(--white); }
  .back-lockup .brand-name { color: var(--white); font-size: 64px; }
  .back-web {
    position: absolute; left: 0; right: 0; top: 300px; text-align: center;
    font-size: 14px; letter-spacing: 5px;
  }
</style>
</head>
<body>
<main class="canvas">

  <section class="card card--front">
    <svg class="front-shape" width="600" height="342" viewBox="0 0 600 342" aria-hidden="true">
      <circle cx="414" cy="171" r="180" fill="var(--ring-grey)"/>
      <circle cx="418" cy="171" r="175" fill="var(--white)"/>
      <circle cx="420" cy="171" r="173" fill="var(--panel-light)"/>
      <rect x="420" y="0" width="180" height="342" fill="var(--panel-light)"/>
    </svg>

    <div class="contact-block">
      <h1 class="person-name">HARRIET DUNMORE</h1>
      <p class="person-role">CEO/FOUNDER</p>
      <p class="address">Brackwell House<br>Norwich QB9 3KX</p>
      <ul class="contact-list">
        <li class="contact-item">
          <svg class="contact-icon" viewBox="0 0 16 16"><path d="M3.5 1l2.5 3-1.5 2c1 2 3 4 5 5l2-1.5 3 2.5-1.5 2.5C8 15 1 8 1.5 2.5z"/></svg>01632 960418
        </li>
        <li class="contact-item">
          <svg class="contact-icon" viewBox="0 0 16 16"><path d="M4 0h8v16H4zM5.5 2v10h5V2zM7 13.2h2v1.3H7z" fill-rule="evenodd"/></svg>07700 900582
        </li>
        <li class="contact-item">
          <svg class="contact-icon" viewBox="0 0 16 16"><path d="M4 1h8v4H4zM1 6h14v6h-2v-2H3v2H1zM4 11h8v4H4z"/></svg>01632 960733
        </li>
        <li class="contact-item">
          <svg class="contact-icon" viewBox="0 0 16 16"><path d="M1 3h14v1L8 9 1 4zM1 5.5l7 5 7-5V13H1z"/></svg>Harriet@plavex.co.uk
        </li>
        <li class="contact-item">
          <svg class="contact-icon" viewBox="0 0 16 16"><circle cx="8" cy="8" r="7"/><path d="M5 4c2 1 1 3 3 3s1 3 3 3c0 2-2 3-2 3" stroke="var(--brand-green)" stroke-width="1.5" fill="none"/></svg>www.plavex.co.uk
        </li>
      </ul>
    </div>

    <div class="brand-lockup">
      <span class="brand-dot"></span>
      <span class="brand-name">Plavex</span>
    </div>
  </section>

  <section class="card card--back">
    <div class="back-lockup">
      <span class="brand-dot"></span>
      <span class="brand-name">Plavex</span>
    </div>
    <p class="back-web">www.plavex.co.uk</p>
  </section>

</main>
</body>
</html>
```